redesign of my existing custom website into Wordpress based website

I need someone to redesign my current website into something more classy, simplistic, modern and on trend. I would like it set up on Wordpress in a way thats easy for me to make my own additions to blogs/price changes and promotion banners. I will also need a page that is password protected so members can login and have access to all my training videos and resources.
website is www.tidewellmamas.com.au

Target Market(s)

new mums

Industry/Entity Type

Fitness

Coding

Coded - Design and coding required

Number of Pages Required

5+ page

Colors
33a6d7

Requirements
Must have
• chic, modern, stylish and simplistic.
• a call to action above the page fold
• mobile friendly conversion
• a pop up message as soon as someone enters my sight offering my free report
• a members page that is password protected containing 3 youtube videos and 6 pdf attachments as resources
• a home page
• a contact us page
• an about us page
• a blog page
• a store page
Nice to have
• some examples of my peers websites that I like:
• www.norapellwick.com
• https://www.9qlr.com
• https://41bytedgarth.com
Should not have
• anything gimmicky

```html
<!DOCTYPE html>
<html lang="en">
<head>
<meta charset="utf-8">
<title>Tidewell Mamas – 12 Week Challenge</title>
<link rel="stylesheet" href="https://fonts.googleapis.com/css2?family=Lato:ital,wght@0,400;0,700;0,900;1,400;1,700;1,900&display=swap">
<style>
:root{
  --blue:#33a6d7;
  --blue-dark:#2b93c0;
  --ink:#2f2f2f;
  --muted:#666;
  --pink:#e0306d;
  --pale:#eef2f5;
  --line:#e3e3e3;
  --white:#fff;
}
*{box-sizing:border-box;margin:0;padding:0}
html,body{width:1200px;height:3930px;overflow:hidden}
body{font-family:"Lato",Arial,sans-serif;color:var(--ink);background:var(--white);position:relative}
.btn{display:inline-block;border-radius:40px;font-weight:700;font-size:15px;letter-spacing:.5px;text-transform:uppercase;text-align:center;line-height:50px;height:50px;padding:0 34px;color:var(--white);background:var(--blue);text-decoration:none}
.btn-ghost{background:transparent;border:2px solid rgba(255,255,255,.8);line-height:46px}
.check-list{list-style:none}
.check-list li{position:relative;padding-left:34px;font-size:15px;line-height:22px;color:#444;margin-bottom:24px}
.check-list svg{position:absolute;left:0;top:2px}

/* nav */
.site-nav{position:absolute;top:0;left:0;width:1200px;height:92px;border-top:5px solid var(--blue);background:var(--white);box-shadow:0 1px 4px rgba(0,0,0,.06)}
.brand{position:absolute;left:100px;top:18px;display:flex;align-items:center;gap:10px;font-size:22px;font-weight:700;color:var(--ink)}
.brand-dot{width:50px;height:50px;border-radius:50%;border:3px solid var(--ink)}
.menu{position:absolute;right:100px;top:28px;display:flex;align-items:center;gap:30px;font-size:15px;font-weight:700;text-transform:uppercase}
.menu .current{color:var(--blue)}
.menu .pill{border-radius:20px;height:34px;line-height:30px;padding:0 16px;font-size:13px}
.menu .login{border:2px solid #ccc;color:var(--ink)}
.menu .join{background:var(--blue);color:var(--white);border:2px solid var(--blue)}

/* hero */
.hero{position:absolute;top:92px;left:0;width:1200px;height:490px;background:linear-gradient(90deg,#3c444d 0%,#4b535c 55%,#5c6470 100%)}
.hero-photo{position:absolute;right:0;top:0;width:470px;height:490px;background:radial-gradient(ellipse at 55% 45%,#c9a58c 0%,#8e7464 40%,#4e555e 75%)}
.hero-copy{position:absolute;left:100px;top:110px;color:var(--white)}
.hero-kicker{font-style:italic;font-size:24px;margin-bottom:14px}
.hero-title{font-size:40px;font-weight:700;line-height:50px;width:620px}
.hero-sub{font-size:24px;margin:14px 0 30px}
.hero-copy .btn{margin-right:20px;width:170px;padding:0}

/* tips band */
.tips{position:absolute;top:582px;left:0;width:1200px;height:204px;background:var(--pale)}
.tips h3{position:absolute;left:100px;top:42px;color:var(--blue);font-size:24px;font-weight:700}
.tips p{position:absolute;left:100px;top:84px;font-size:17px;color:#444}
.tips h2{position:absolute;left:100px;top:118px;font-size:38px;font-weight:900;font-style:italic}
.tips .btn{position:absolute;right:100px;top:76px;width:230px;padding:0}

/* why */
.why{position:absolute;top:786px;left:0;width:1200px;height:524px}
.why h2{position:absolute;left:100px;top:60px;width:460px;font-size:30px;line-height:40px;font-weight:700}
.why .check-list{position:absolute;left:100px;top:170px;width:440px}
.video{position:absolute;left:608px;top:130px;width:492px;height:290px;background:linear-gradient(135deg,#5a4a44,#2c2a2e 60%,#6d6a72)}
.video svg{position:absolute;left:214px;top:113px}

/* cta band */
.cta-band{position:absolute;top:1310px;left:0;width:1200px;height:275px;background:linear-gradient(180deg,#e6e6e6,#d2d2d2)}
.cta-band h2{margin-top:52px;text-align:center;font-size:30px;font-weight:700;color:#333}
.cta-band h2 u{text-underline-offset:5px}
.cta-band p{text-align:center;font-size:17px;color:#444;margin:16px 0 28px}
.cta-band .btn{position:absolute;left:480px;top:168px;width:240px;padding:0}

/* results */
.results{position:absolute;top:1585px;left:0;width:1200px;height:590px;background:linear-gradient(180deg,#3e3b3c,#2a2829)}
.results h2{margin:54px auto 0;width:680px;text-align:center;color:var(--white);font-size:30px;line-height:40px;font-weight:700}
.result-cards{position:absolute;left:100px;top:176px;display:flex;gap:18px}
.result-card{width:237px;height:356px;background:var(--white);text-align:center}
.result-photo{height:168px;background:linear-gradient(135deg,#b48e78,#e3d2c6 50%,#9a8578)}
.result-card h4{font-size:17px;font-weight:700;margin-top:18px}
.result-card .role{font-size:11px;color:var(--muted)}
.result-card .stat{color:var(--pink);font-size:16px;font-weight:700;line-height:20px;margin:6px 16px}
.result-card p.quote{font-size:11px;line-height:15px;color:#555;margin:8px 16px}

/* included */
.included{position:absolute;top:2175px;left:0;width:1200px;height:589px}
.collage{position:absolute;left:100px;top:62px;width:492px;height:348px;display:flex;gap:6px}
.collage div{flex:1}
.collage .a{background:linear-gradient(180deg,#8a7b72,#4c4a4f)}
.collage .b{background:linear-gradient(180deg,#d34b8c,#e9c9a1 55%,#b68a5c)}
.collage .c{background:linear-gradient(180deg,#7c7a7e,#3f3c40)}
.included h2{position:absolute;left:652px;top:62px;font-size:30px;font-weight:700}
.included .check-list{position:absolute;left:652px;top:122px;width:440px}
.included .check-list li{margin-bottom:18px}
.price{position:absolute;left:652px;top:388px;font-size:17px;font-weight:700}
.price small{display:block;font-size:11px;font-weight:400;color:var(--muted);margin-top:4px}
.included .btn{position:absolute;left:652px;top:488px;width:228px;padding:0}

/* news */
.news{position:absolute;top:2764px;left:0;width:1200px;height:563px;background:linear-gradient(180deg,#eef3f7,#f7f9fb)}
.news h2{text-align:center;margin-top:54px;font-size:30px;font-weight:700}
.news-cards{position:absolute;left:100px;top:140px;display:flex;gap:18px}
.news-card{width:237px;height:380px;background:var(--white);box-shadow:0 2px 6px rgba(0,0,0,.08);text-align:center}
.news-img{height:172px}
.news-card h4{font-size:14px;font-weight:700;line-height:19px;margin:24px 20px 12px;height:38px}
.news-card p{font-size:11px;line-height:15px;color:#777;margin:0 22px}
.news-meta{margin-top:22px;font-size:13px;font-weight:700;color:var(--blue);display:flex;justify-content:center;gap:24px;align-items:center}

/* quote */
.founder{position:absolute;top:3333px;left:0;width:1200px;height:269px;background:var(--blue)}
.founder-photo{position:absolute;left:0;top:0;width:320px;height:269px;background:linear-gradient(135deg,#e4d3c9,#b4978a 55%,#7e6a62)}
.founder blockquote{position:absolute;left:365px;top:42px;width:740px;color:var(--white);font-style:italic;font-size:15px;line-height:24px;font-weight:700}
.founder cite{display:block;margin-top:18px;font-size:20px;font-weight:900}

/* footer */
.site-footer{position:absolute;top:3602px;left:0;width:1200px;height:328px}
.footer-brand{position:absolute;left:100px;top:76px;display:flex;align-items:center;gap:12px;font-size:24px;font-weight:700}
.footer-brand .brand-dot{width:90px;height:90px}
.footer-col{position:absolute;top:54px}
.footer-col h5{font-size:18px;font-weight:700;margin-bottom:14px}
.footer-col li{list-style:none;font-size:12px;line-height:18px;color:#666}
.footer-col p{font-size:12px;line-height:18px;color:#666;width:200px}
.footer-col .btn{height:36px;line-height:36px;font-size:11px;padding:0 22px;margin-top:16px}
.social{display:flex;align-items:center;gap:12px;font-size:12px;color:#666;margin-bottom:16px}
.social span.sq{width:28px;height:28px;background:#777}
.copyright{position:absolute;left:100px;right:100px;top:256px;border-top:1px solid var(--line);padding-top:14px;text-align:center;font-size:11px;color:#888}
</style>
</head>
<body>

<header class="site-nav">
  <div class="brand"><span class="brand-dot"></span>Tidewell Mamas</div>
  <nav class="menu">
    <span class="current">Home</span><span>About Us</span><span>Program</span><span>Blog</span><span>FAQ</span><span>Contact Us</span>
    <span class="pill login">Login</span><span class="pill join">Join Now</span>
  </nav>
</header>

<section class="hero">
  <div class="hero-photo" role="img" aria-label="Smiling founder in workout top against a dark wall"></div>
  <div class="hero-copy">
    <p class="hero-kicker">Transform your body and mind in just 12 weeks with my</p>
    <h1 class="hero-title">Tidewell Mamas 12 week Challenge</h1>
    <p class="hero-sub">and do it from the comfort of your own home</p>
    <a class="btn">Learn More ⊕</a><a class="btn btn-ghost">Join Now</a>
  </div>
</section>

<section class="tips">
  <h3>Bounce Back into a Fitter, Healthier, More Energetic you!</h3>
  <p>Let me share with you some of my best secrets to bouncing back after baby with my FREE</p>
  <h2>Top 10 Bouncing Back Tips</h2>
  <a class="btn">Get It Free Now!</a>
</section>

<section class="why">
  <h2>Why choose the Tidewell Mamas 12 Week Challenge</h2>
  <ul class="check-list">
    <li><svg width="18" height="18"><circle cx="9" cy="9" r="9" fill="#33a6d7"/><path d="M5 9l3 3 5-6" stroke="#fff" stroke-width="2" fill="none"/></svg>A program uniquely tailored to suit bodies post pregnancy</li>
    <li><svg width="18" height="18"><circle cx="9" cy="9" r="9" fill="#33a6d7"/><path d="M5 9l3 3 5-6" stroke="#fff" stroke-width="2" fill="none"/></svg>A workout program that grows with you as your fitness and strength improve</li>
    <li><svg width="18" height="18"><circle cx="9" cy="9" r="9" fill="#33a6d7"/><path d="M5 9l3 3 5-6" stroke="#fff" stroke-width="2" fill="none"/></svg>Proven training methods built by a post pregnancy specialist trainer and mum</li>
    <li><svg width="18" height="18"><circle cx="9" cy="9" r="9" fill="#33a6d7"/><path d="M5 9l3 3 5-6" stroke="#fff" stroke-width="2" fill="none"/></svg>A dedicated focus on rebuilding core strength</li>
    <li><svg width="18" height="18"><circle cx="9" cy="9" r="9" fill="#33a6d7"/><path d="M5 9l3 3 5-6" stroke="#fff" stroke-width="2" fill="none"/></svg>Delicious and healthy family friendly recipes</li>
    <li><svg width="18" height="18"><circle cx="9" cy="9" r="9" fill="#33a6d7"/><path d="M5 9l3 3 5-6" stroke="#fff" stroke-width="2" fill="none"/></svg>The ultimate convenience of being able to train from home, anytime you want!</li>
  </ul>
  <div class="video" role="img" aria-label="Workout video still of a mum exercising on a mat beside her baby in a living room">
    <svg width="64" height="64"><circle cx="32" cy="32" r="32" fill="rgba(255,255,255,.9)"/><path d="M25 19l22 13-22 13z" fill="#333"/></svg>
  </div>
</section>

<section class="cta-band" role="img" aria-label="Soft faded photo of a home workout space behind the call to action">
  <h2>Don’t waste anymore time <u>Thinking</u> about getting back into shape</h2>
  <p>Take the first step to a fitter healthier more energetic you and join our program today!</p>
  <a class="btn">Get Started Now!</a>
</section>

<section class="results">
  <h2>Check out some of the awesome results already achieved by mums on our challenge</h2>
  <div class="result-cards">
    <article class="result-card">
      <div class="result-photo" role="img" aria-label="Before and after photos of Marla"></div>
      <h4>Marla</h4><div class="role">Tidewell Mamas Founder</div>
      <div class="stat">Lost 15kgs and 25cms in 12 weeks</div>
      <p class="quote">This is the exact program I used after 2 of my babies and I lost around 15kg in 12 weeks both times.</p>
    </article>
    <article class="result-card">
      <div class="result-photo" role="img" aria-label="Before and after photos of Lena"></div>
      <h4>Lena</h4>
      <div class="stat">Lost 10kgs in 12 weeks</div>
      <p class="quote">Its rare a program delivers what it promises and everyone should know yours is the real deal!</p>
    </article>
    <article class="result-card">
      <div class="result-photo" role="img" aria-label="Before and after photos of Brielle"></div>
      <h4>Brielle</h4>
      <div class="stat">Lost 20cms in 12 weeks</div>
      <p class="quote">I am really happy with my results, I have lost 20cms across my body and lost 8kg, but most importantly my flabby tummy is gone and I feel toned all over</p>
    </article>
    <article class="result-card">
      <div class="result-photo" role="img" aria-label="Before and after photos of KT"></div>
      <h4>KT</h4>
      <div class="stat">Lost 18cms in 12 weeks</div>
      <p class="quote">This program was exactly what I needed! Within a matter of months I was back in my old clothes and had people commenting about how quickly I had bounced back</p>
    </article>
  </div>
</section>

<section class="included">
  <div class="collage">
    <div class="a" role="img" aria-label="Trainer lifting dumbbells"></div>
    <div class="b" role="img" aria-label="Healthy eating guide cover with meal photos"></div>
    <div class="c" role="img" aria-label="Trainer doing a step workout"></div>
  </div>
  <h2>What's included in the program?</h2>
  <ul class="check-list">
    <li><svg width="18" height="18"><circle cx="9" cy="9" r="9" fill="#33a6d7"/><path d="M5 9l3 3 5-6" stroke="#fff" stroke-width="2" fill="none"/></svg>Our unique 3 stage, cardio, resistance and core, 12 week training program</li>
    <li><svg width="18" height="18"><circle cx="9" cy="9" r="9" fill="#33a6d7"/><path d="M5 9l3 3 5-6" stroke="#fff" stroke-width="2" fill="none"/></svg>Full instructional online workout videos and program cards for each program</li>
    <li><svg width="18" height="18"><circle cx="9" cy="9" r="9" fill="#33a6d7"/><path d="M5 9l3 3 5-6" stroke="#fff" stroke-width="2" fill="none"/></svg>Weekly accountability charts</li>
    <li><svg width="18" height="18"><circle cx="9" cy="9" r="9" fill="#33a6d7"/><path d="M5 9l3 3 5-6" stroke="#fff" stroke-width="2" fill="none"/></svg>Weekly coaching emails</li>
    <li><svg width="18" height="18"><circle cx="9" cy="9" r="9" fill="#33a6d7"/><path d="M5 9l3 3 5-6" stroke="#fff" stroke-width="2" fill="none"/></svg>Nutritionist approved healthy eating guide</li>
    <li><svg width="18" height="18"><circle cx="9" cy="9" r="9" fill="#33a6d7"/><path d="M5 9l3 3 5-6" stroke="#fff" stroke-width="2" fill="none"/></svg>Healthy Family Favourites recipe ebook</li>
  </ul>
  <div class="price">All for just $89<small>One time only payment</small></div>
  <a class="btn">Get Started Now!</a>
</section>

<section class="news">
  <h2>Top News</h2>
  <div class="news-cards">
    <article class="news-card">
      <div class="news-img" role="img" aria-label="Trainer stretching in a gym" style="background:linear-gradient(135deg,#6e6a6c,#2f2d30)"></div>
      <h4>The benefits of training in the morning</h4>
      <p>Cum soluta nobis est  nihil impedit quo minus id quod maxime place acere possimu...</p>
      <div class="news-meta"><span>JAN 02</span><span>♥ 21</span></div>
    </article>
    <article class="news-card">
      <div class="news-img" role="img" aria-label="Trainer doing a lounge room cardio move" style="background:linear-gradient(135deg,#8b6d68,#2d2b2e)"></div>
      <h4>Marla's 10 exercise lounge room cardio workout</h4>
      <p>Cum soluta nobis est  nihil impedit quo minus id quod maxime place acere possimu...</p>
      <div class="news-meta"><span>JAN 02</span><span>♥ 21</span></div>
    </article>
    <article class="news-card">
      <div class="news-img" role="img" aria-label="Golden pies on a white plate" style="background:linear-gradient(135deg,#d7c7a9,#9d8258)"></div>
      <h4>Healthy Shepherds Pie Recipe</h4>
      <p>Cum soluta nobis est  nihil impedit quo minus id quod maxime place acere possimu...</p>
      <div class="news-meta"><span>JAN 02</span><span>♥ 21</span></div>
    </article>
    <article class="news-card">
      <div class="news-img" role="img" aria-label="Chocolate treats on a dark table" style="background:linear-gradient(135deg,#5a3a2a,#c27a42)"></div>
      <h4>Dairy, Gluten, Sugar, Guilt Free Easter the morning</h4>
      <p>Cum soluta nobis est  nihil impedit quo minus id quod maxime place acere possimu...</p>
      <div class="news-meta"><span>JAN 02</span><span>♥ 21</span></div>
    </article>
  </div>
</section>

<section class="founder">
  <div class="founder-photo" role="img" aria-label="Founder holding her baby"></div>
  <blockquote>As a mother of 3 beautiful babies I know exactly how hard it can be to find the time and energy to focus on yourself. That's why I designed a program that was easy to follow, could fit into the life of a busy mum and was focused on all the areas that need attention after babies. I'm so passionate about sharing what I have learnt through all my post pregnancy training courses and time spent with physio's and hope I can also help you to become a fitter, healthier more energetic you!
    <cite>- Marla Devens</cite>
  </blockquote>
</section>

<footer class="site-footer">
  <div class="footer-brand"><span class="brand-dot"></span>Tidewell Mamas</div>
  <div class="footer-col" style="left:382px">
    <h5>Quick Links</h5>
    <ul><li>Home</li><li>About Us</li><li>Program</li><li>Blog</li><li>Shop</li><li>Contact Us</li></ul>
  </div>
  <div class="footer-col" style="left:556px">
    <h5>Subscribe</h5>
    <p>Register your details below and receive tones of free information on fitness and living a healthy lifestyle</p>
    <a class="btn">Subscribe</a>
  </div>
  <div class="footer-col" style="left:892px">
    <h5>Stay Connected</h5>
    <div class="social"><span class="sq"></span>Friendpage</div>
    <div class="social"><span class="sq"></span>Snapgrid</div>
  </div>
  <div class="copyright">Copyright © 2017, Tidewell Mamas. All rights reserved</div>
</footer>

</body>
</html>
```